KBT Business Cards

We require business cards for our business. We would like a matte black back to the card, with our logo centred in the middle. The front side of the card is open to design.

Target Market(s)

Clients looking for legal services (professional)

Industry/Entity Type

Legal

Contact Information for Business Card

Doran Kelbrath
Partner
Mobile: 0461 738 524
Email: doran@kbtlaw.co
Website: www.kbtlaw.co
Level 3, 118 Wendmore Street
Sydney NSW 2000

Font styles to use
Other font styles liked:
• Avenir

Colors
f04a50
ffffff
1b1b1b

Requirements
Must have
• Black back with logo included in the centre of the card.
• Our font is Avenir.

```html
<!DOCTYPE html>
<html lang="en">
<head>
<meta charset="utf-8">
<title>KBT Business Cards</title>
<link rel="stylesheet" href="https://fonts.googleapis.com/css2?family=Nunito+Sans:wght@400;600;700;800&display=swap">
<style>
  :root {
    --brand-pink: #d8265e;
    --brand-red: #f04a50;
    --ink: #1b1b1b;
    --paper: #ffffff;
    --stage: #e7e4df;
    --muted: #3a3a3a;
  }
  * { box-sizing: border-box; margin: 0; padding: 0; }
  html, body { width: 1200px; height: 780px; overflow: hidden; }
  body {
    background: var(--stage);
    font-family: "Nunito Sans", "Avenir", sans-serif;
    display: flex;
    align-items: center;
    justify-content: center;
    gap: 40px;
  }
  .card {
    position: relative;
    width: 540px;
    height: 310px;
    border-radius: 22px;
    overflow: hidden;
    box-shadow: 0 10px 28px rgba(0,0,0,.18), 0 2px 4px rgba(0,0,0,.12);
  }
  .card-front { background: var(--paper); }
  .card-back { background: var(--ink); display: flex; align-items: center; justify-content: center; }

  .front-band { position: absolute; inset: 0; width: 100%; height: 100%; }

  .holder {
    position: absolute;
    top: 6px;
    right: 26px;
    text-align: right;
    color: var(--paper);
    line-height: 1.1;
  }
  .holder-name { font-size: 13px; font-weight: 800; letter-spacing: .3px; }
  .holder-role { font-size: 10px; font-weight: 400; }

  .firm-mark {
    display: flex;
    align-items: center;
    gap: 12px;
  }
  .firm-square {
    width: 34px;
    height: 34px;
    background: var(--brand-pink);
    flex: none;
  }
  .firm-name {
    font-weight: 800;
    font-size: 17px;
    line-height: 1.02;
    letter-spacing: .4px;
    text-transform: uppercase;
  }
  .card-front .firm-mark { position: absolute; left: 42px; top: 180px; }
  .card-front .firm-name { color: var(--ink); }

  .contact-rule {
    position: absolute;
    left: 42px;
    top: 244px;
    width: 210px;
    height: 1px;
    background: var(--brand-pink);
  }
  .contact-list {
    position: absolute;
    left: 42px;
    top: 252px;
    list-style: none;
    font-size: 11px;
    color: var(--muted);
    line-height: 16px;
  }
  .contact-list li { display: flex; align-items: center; gap: 8px; }
  .contact-dot {
    width: 11px; height: 11px;
    border-radius: 50%;
    border: 2px solid var(--brand-pink);
    background: radial-gradient(circle, var(--brand-pink) 0 2.5px, transparent 3px);
    flex: none;
  }

  .section-divider {
    position: absolute;
    left: 282px;
    top: 206px;
    width: 1px;
    height: 34px;
    background: var(--brand-pink);
  }

  .office {
    position: absolute;
    left: 310px;
    top: 140px;
    width: 200px;
  }
  .office-rule { height: 1px; background: var(--brand-pink); margin-bottom: 8px; }
  .office-firm {
    font-size: 11.5px;
    font-weight: 800;
    color: var(--brand-pink);
    text-transform: uppercase;
    letter-spacing: .3px;
  }
  .office-address { font-size: 11px; color: var(--muted); line-height: 15px; font-style: normal; }

  .card-back .firm-square { background: var(--brand-red); width: 44px; height: 44px; }
  .card-back .firm-name { color: var(--paper); font-size: 22px; }
</style>
</head>
<body>

  <section class="card card-front" aria-label="Business card front">
    <svg class="front-band" viewBox="0 0 540 310" preserveAspectRatio="none" aria-hidden="true">
      <path d="M0 0 H540 V38 Q300 44 0 182 Z" fill="var(--brand-pink)"/>
      <path d="M34 186 Q290 62 540 46 V53 Q300 72 34 186 Z" fill="var(--ink)"/>
    </svg>

    <div class="holder">
      <div class="holder-name">DORAN KELBRATH</div>
      <div class="holder-role">Partner</div>
    </div>

    <div class="firm-mark">
      <span class="firm-square"></span>
      <span class="firm-name">Kelbrath<br>Bryce<br>Tannard</span>
    </div>

    <div class="contact-rule"></div>
    <ul class="contact-list">
      <li><span class="contact-dot"></span>0461 738 524</li>
      <li><span class="contact-dot"></span>doran@kbtlaw.co</li>
      <li><span class="contact-dot"></span>www.kbtlaw.co</li>
    </ul>

    <div class="section-divider"></div>

    <div class="office">
      <div class="office-rule"></div>
      <div class="office-firm">Kelbrath Bryce Tannard</div>
      <address class="office-address">Level 3, 118 Wendmore Street<br>Sydney NSW 2000</address>
    </div>
  </section>

  <section class="card card-back" aria-label="Business card back">
    <div class="firm-mark">
      <span class="firm-square"></span>
      <span class="firm-name">Kelbrath<br>Bryce<br>Tannard</span>
    </div>
  </section>

</body>
</html>
```